Flyer for the Lumen 2025 Conference

I am looking to produce a flyer for our upcoming conference, Lumen 2025. This is an annual conference that we plan to publicize on social media. The ideal designer will create a flyer that is eye-catching and effectively communicates the key information. Please see attached our logo, speaker photo, and flyer content.

Target Market(s)

All demographics

Industry/Entity Type

Christian

Font styles to use
Sans Serif

Requirements
Should not have
• Cross, church

```html
<!DOCTYPE html>
<html lang="en">
<head>
<meta charset="utf-8">
<title>Lumen 2025 Conference Flyer</title>
<link href="https://fonts.googleapis.com/css2?family=Anton&family=Montserrat:wght@200;300;400;500;600;700;800;900&display=swap" rel="stylesheet">
<style>
  :root{
    --navy-deep:#020a2a;
    --navy:#06164f;
    --royal:#1d4fd6;
    --glow:#2f6cff;
    --orange:#f7941d;
    --gold:#f9b233;
    --cyan:#1fc8e6;
    --teal:#11a9c4;
    --white:#ffffff;
    --soft-white:#f3e9df;
    --bar-start:#1ab6f0;
    --bar-end:#27e2ea;
    --ink:#0b1a3a;
  }
  *{margin:0;padding:0;box-sizing:border-box}
  html,body{width:927px;height:1200px;overflow:hidden;background:var(--navy-deep)}
  body{font-family:"Montserrat",sans-serif;color:var(--white)}
  .flyer{
    position:relative;width:927px;height:1200px;overflow:hidden;
    background:
      radial-gradient(ellipse 380px 420px at 470px 230px, rgba(47,108,255,.55), transparent 70%),
      radial-gradient(ellipse 360px 300px at 330px 820px, rgba(47,108,255,.45), transparent 70%),
      linear-gradient(180deg,#0a2a8c 0%,#082070 35%,#051650 65%,var(--navy-deep) 100%);
  }
  .mic-photo{
    position:absolute;left:640px;top:90px;width:287px;height:330px;
    background:radial-gradient(ellipse at 55% 45%, rgba(40,80,190,.55), rgba(5,20,70,.2) 70%, transparent);
  }
  .speaker-photo{
    position:absolute;left:0;top:380px;width:530px;height:755px;
    background:linear-gradient(160deg, rgba(40,100,230,.75) 0%, rgba(20,60,180,.7) 45%, rgba(8,25,90,.6) 100%);
    border-radius:220px 220px 0 0;
  }
  .topic{position:absolute;left:68px;top:54px}
  .topic .label{color:var(--orange);font-size:24px;font-weight:300}
  .topic .title{font-size:30px;font-weight:300;line-height:33px;margin-top:4px}
  .topic .title b{font-weight:500}
  .divider-v{position:absolute;left:69px;top:160px;width:1px;height:385px;background:rgba(255,255,255,.8)}
  .brand{position:absolute;left:370px;top:66px;width:195px;text-align:center}
  .brand .name{font-size:38px;font-weight:500;letter-spacing:1px;line-height:40px;color:var(--white)}
  .brand .tagline{font-size:9px;color:var(--gold);letter-spacing:.5px;margin-top:3px;white-space:nowrap}
  .event-name{position:absolute;left:277px;top:128px;width:375px;text-align:center;font-family:"Anton",sans-serif;line-height:1}
  .event-name .word{display:block;font-size:150px;letter-spacing:2px;
    background:linear-gradient(180deg,var(--gold),var(--orange));-webkit-background-clip:text;background-clip:text;color:transparent}
  .event-name .year{display:block;font-size:182px;margin-top:-6px;color:var(--soft-white)}
  .subtitle{position:absolute;left:287px;top:476px;width:380px;white-space:nowrap}
  .subtitle .strong{font-size:44px;font-weight:900;line-height:50px;letter-spacing:.5px;
    background:linear-gradient(90deg,#0e8aa8,var(--cyan));-webkit-background-clip:text;background-clip:text;color:transparent}
  .subtitle .light{font-size:47px;font-weight:200;line-height:58px;color:#dfe6f5;letter-spacing:1px}
  .month{position:absolute;left:478px;top:906px;transform:rotate(-90deg);transform-origin:left top;
    font-size:38px;font-weight:800;color:var(--teal);letter-spacing:.5px;line-height:34px}
  .schedule{position:absolute;left:525px;top:710px;width:320px}
  .session{position:relative;height:55px;margin-bottom:7px;display:flex;align-items:center}
  .session::before{content:"";position:absolute;left:80px;top:0;width:240px;height:100%;
    background:linear-gradient(90deg,rgba(13,40,120,0) 0%,rgba(30,110,220,.85) 20%,rgba(20,80,200,.6) 75%,rgba(20,60,180,0) 100%)}
  .session .day-num{position:relative;width:125px;font-size:44px;font-weight:800;letter-spacing:-1px;
    background:linear-gradient(180deg,var(--gold),var(--orange));-webkit-background-clip:text;background-clip:text;color:transparent}
  .session .day-num sup{font-size:24px;vertical-align:18px}
  .session .when{position:relative;line-height:21px}
  .session .weekday{font-size:18px;font-weight:400}
  .session .time{font-size:17px;font-weight:700}
  .rule{position:absolute;left:525px;width:334px;height:1px;background:var(--cyan)}
  .venue{position:absolute;left:525px;top:935px;font-size:16.5px;font-weight:700;color:var(--orange);letter-spacing:.3px}
  .pin{position:absolute;left:525px;top:966px;width:42px;height:40px;border-radius:10px;
    background:linear-gradient(135deg,var(--cyan),#1a7fe0);display:flex;align-items:center;justify-content:center}
  .address{position:absolute;left:578px;top:966px;font-size:17px;line-height:19px;letter-spacing:1.3px;font-weight:400}
  .app-note{position:absolute;left:527px;top:1046px;font-size:20px;line-height:22px;font-weight:400}
  .app-note .hl-orange{color:var(--orange);font-weight:600}
  .app-note .hl-cyan{color:var(--cyan);font-weight:600}
  .store-badge{position:absolute;left:770px;width:87px;height:30px;border:1px solid rgba(255,255,255,.9);border-radius:5px;background:#000}
  .speaker{position:absolute;left:68px;top:1018px}
  .speaker .label{font-size:28px;font-weight:300;color:var(--orange);line-height:32px}
  .speaker .name{font-size:31px;font-weight:800;line-height:33px;letter-spacing:.3px}
  .contact-bar{position:absolute;left:0;top:1133px;width:927px;height:32px;
    background:linear-gradient(90deg,var(--bar-start),var(--bar-end));display:flex;align-items:center;
    color:var(--ink);font-size:20px;letter-spacing:1.4px;font-weight:400}
  .contact-bar .item{position:absolute;display:flex;align-items:center;gap:8px}
  .footer{position:absolute;left:0;top:1165px;width:927px;height:35px;background:#000}
</style>
</head>
<body>
<div class="flyer">
  <div class="mic-photo" role="img" aria-label="Dimly lit stage microphone against blue bokeh lights"></div>
  <div class="speaker-photo" role="img" aria-label="Portrait of the speaker seated in a blue suit"></div>

  <div class="topic">
    <div class="label">Topic:</div>
    <div class="title">The <b>Voice</b><br>Of The <b>Lord</b></div>
  </div>
  <div class="divider-v"></div>

  <div class="brand">
    <div class="name">KAVEL</div>
    <div class="tagline">SHINING ACROSS EVERY SHORE</div>
  </div>

  <h1 class="event-name"><span class="word">LUMEN</span><span class="year">2025</span></h1>

  <div class="subtitle">
    <div class="strong">A PROPHETIC</div>
    <div class="light">CONFERENCE</div>
  </div>

  <div class="month">December</div>
  <div class="schedule">
    <div class="session"><div class="day-num">26<sup>th</sup></div><div class="when"><div class="weekday">Friday</div><div class="time">6:30PM - 9:00PM</div></div></div>
    <div class="session"><div class="day-num">27<sup>th</sup></div><div class="when"><div class="weekday">Saturday</div><div class="time">5:30PM &nbsp;- 8:00PM</div></div></div>
    <div class="session"><div class="day-num">28<sup>th</sup></div><div class="when"><div class="weekday">Sunday</div><div class="time">4:30PM - 7:00PM</div></div></div>
  </div>

  <div class="rule" style="top:915px"></div>
  <div class="venue">The Harborview Performing Arts Center</div>
  <div class="pin">
    <svg width="20" height="26" viewBox="0 0 20 26"><path d="M10 1C5 1 1.5 4.8 1.5 9.5 1.5 16 10 25 10 25s8.5-9 8.5-15.5C18.5 4.8 15 1 10 1z" fill="#0b1a3a"/><circle cx="10" cy="9.5" r="3.6" fill="#1fc8e6"/></svg>
  </div>
  <div class="address">318 Alder Grove Street<br>Brookfield, Maine 04011</div>
  <div class="rule" style="top:1032px"></div>

  <div class="app-note"><span class="hl-orange">Download</span> the<br><span class="hl-cyan">KAVEL App</span> to stay<br>updated on the event</div>
  <div class="store-badge" style="top:1045px"></div>
  <div class="store-badge" style="top:1080px"></div>

  <div class="speaker">
    <div class="label">SPEAKER:</div>
    <div class="name">PROPHET<br>ELIAS MWANGI</div>
  </div>

  <div class="contact-bar">
    <div class="item" style="left:68px">
      <svg width="20" height="20" viewBox="0 0 20 20" fill="none" stroke="#0b1a3a" stroke-width="2"><circle cx="10" cy="10" r="8.5"/><ellipse cx="10" cy="10" rx="3.8" ry="8.5"/><path d="M1.5 10h17M3 5.5h14M3 14.5h14"/></svg>
      <span>www.kavel.org</span>
    </div>
    <div class="item" style="left:358px">
      <svg width="18" height="18" viewBox="0 0 24 24"><path fill="#0b1a3a" d="M6.6 10.8a15.2 15.2 0 0 0 6.6 6.6l2.2-2.2c.3-.3.7-.4 1-.2 1.1.4 2.3.6 3.6.6.6 0 1 .4 1 1V20c0 .6-.4 1-1 1C10.6 21 3 13.4 3 4c0-.6.4-1 1-1h3.5c.6 0 1 .4 1 1 0 1.3.2 2.5.6 3.6.1.3 0 .7-.2 1z"/></svg>
      <span>207 555 0142</span>
    </div>
    <div class="item" style="left:620px">
      <svg width="20" height="16" viewBox="0 0 20 16"><rect x="1" y="1" width="18" height="14" rx="2" fill="none" stroke="#0b1a3a" stroke-width="2.2"/><path d="M2 2l8 6.5L18 2" fill="none" stroke="#0b1a3a" stroke-width="2.2"/></svg>
      <span>contact@kavel.org</span>
    </div>
  </div>
  <div class="footer"></div>
</div>
</body>
</html>
```